Sports / Entertainment Media Co needs a biz card design

We are a media co / luxury lifestyle brand that targets professional athletes, entertainers and high net-worth fans. We are currently preparing for a relaunch and in need for new biz cards. I envision a black on black card with a pop of color on opposite side. Color Palette black, white, red etc. I want this card to exude sexiness and power. Very high stylized, hip and cool. I have attached the logo - I would like to see it all in black, but also open to other ideas. I will also upload a current card with all information needed on this new card. Furthermore I will add some samples of other cards I love. Thanks!!!
Updates

I provided suggestions, however I am open to all ideas!!   Be as creative as you can.  Think cutting-edge, sexy and powerful.  Take a look at the cards I uploaded to get a sense for what I like.  Thanks!!!

Industry/Entity Type

Entertainment

```html
<!DOCTYPE html>
<html lang="en">
<head>
<meta charset="utf-8">
<title>Pulse – Business Card</title>
<link rel="stylesheet" href="https://fonts.googleapis.com/css2?family=Oswald:wght@500&family=Saira:wght@400;500;700&display=swap">
<style>
  :root {
    --backdrop: #b9b9b9;
    --card: #f7f7f7;
    --card-edge: #e4e4e4;
    --ink: #1b1b1b;
    --ink-soft: #3a3a3a;
    --rule: #2a2a2a;
    --accent: #d3131b;
    --map-tone: #ececec;
  }
  * { box-sizing: border-box; margin: 0; padding: 0; }
  html, body {
    width: 1200px; height: 1002px; overflow: hidden;
    background: var(--backdrop);
  }
  .canvas { position: relative; width: 1200px; height: 1002px; }

  .card {
    position: absolute; left: 190px; width: 820px; height: 460px;
    background: var(--card);
    border: 1px solid var(--card-edge);
    box-shadow: 0 8px 24px rgba(0,0,0,.18);
    overflow: hidden;
  }
  .card--back { top: 29px; background: #fbfbfb; }
  .card--front { top: 513px; }

  /* back face */
  .world-map {
    position: absolute; left: 60px; top: 20px; width: 700px; height: 420px;
    background: radial-gradient(ellipse at 55% 50%, var(--map-tone) 0%, rgba(236,236,236,.5) 55%, rgba(251,251,251,0) 75%);
  }
  .brand {
    position: absolute; display: flex; align-items: center; gap: 14px;
    font-family: "Saira", sans-serif; font-weight: 700; color: var(--ink);
    letter-spacing: -1px; line-height: 1;
  }
  .brand__dot { width: 22px; height: 22px; border-radius: 50%; background: var(--accent); flex: none; }
  .card--back .brand { left: 250px; top: 180px; font-size: 104px; }
  .card--back .brand__dot { width: 28px; height: 28px; }

  /* front face */
  .person { position: absolute; left: 58px; top: 88px; }
  .person__name {
    font-family: "Oswald", sans-serif; font-weight: 500; font-size: 60px;
    line-height: 1; color: var(--ink); letter-spacing: .5px; text-transform: uppercase;
  }
  .person__role {
    margin-top: 6px;
    font-family: "Saira", sans-serif; font-weight: 500; font-size: 22px;
    letter-spacing: 2.5px; color: var(--ink-soft); text-transform: uppercase;
  }
  .rule-h { position: absolute; left: 52px; top: 216px; width: 446px; height: 4px; background: var(--rule); }
  .rule-v { position: absolute; left: 496px; top: 98px; width: 4px; height: 296px; background: var(--rule); }

  .contacts {
    position: absolute; left: 56px; top: 238px; width: 440px;
    display: grid; grid-template-columns: 190px 250px; row-gap: 14px;
    font-family: "Saira", sans-serif; font-size: 15.5px; color: var(--ink); list-style: none;
  }
  .contacts li { display: flex; align-items: center; gap: 9px; white-space: nowrap; }
  .contacts .wide { grid-column: 1 / 3; }
  .contacts svg { width: 16px; height: 16px; flex: none; fill: var(--ink); }

  .card--front .brand { left: 540px; top: 214px; font-size: 80px; }
</style>
</head>
<body>
<main class="canvas">

  <section class="card card--back" aria-label="Card back">
    <div class="world-map" role="img" aria-label="Faint world map in pale grey"></div>
    <div class="brand"><span class="brand__name">pulse</span><span class="brand__dot"></span></div>
  </section>

  <section class="card card--front" aria-label="Card front">
    <div class="person">
      <h1 class="person__name">Marcus Hale</h1>
      <p class="person__role">General Manager</p>
    </div>
    <div class="rule-h"></div>
    <div class="rule-v"></div>

    <ul class="contacts">
      <li>
        <svg viewBox="0 0 24 24" aria-hidden="true"><path d="M6.6 10.8a15.1 15.1 0 0 0 6.6 6.6l2.2-2.2a1 1 0 0 1 1-.25 11.4 11.4 0 0 0 3.6.57 1 1 0 0 1 1 1V20a1 1 0 0 1-1 1A17 17 0 0 1 3 4a1 1 0 0 1 1-1h3.5a1 1 0 0 1 1 1c0 1.25.2 2.45.57 3.57a1 1 0 0 1-.25 1z"/></svg>
        020 555 0148
      </li>
      <li>
        <svg viewBox="0 0 24 24" aria-hidden="true"><path d="M2 5h20v14H2zm2 2v.4l8 5 8-5V7zm0 2.8V17h16V9.8l-8 5z"/></svg>
        marcus@pulsemedia.co
      </li>
      <li>
        <svg viewBox="0 0 24 24" aria-hidden="true"><path d="M7 1h10a2 2 0 0 1 2 2v18a2 2 0 0 1-2 2H7a2 2 0 0 1-2-2V3a2 2 0 0 1 2-2zm0 3v14h10V4zm5 15.5a1.2 1.2 0 1 0 0 2.4 1.2 1.2 0 0 0 0-2.4z"/></svg>
        020 555 0148
      </li>
      <li>
        <svg viewBox="0 0 24 24" aria-hidden="true"><path d="M12 2a10 10 0 1 0 0 20 10 10 0 0 0 0-20zm6.9 6h-3a15.6 15.6 0 0 0-1.3-3.8A8 8 0 0 1 18.9 8zM12 4c.8 1.2 1.5 2.5 1.9 4h-3.8c.4-1.5 1.1-2.8 1.9-4zM4.3 14a8 8 0 0 1 0-4h3.4a16 16 0 0 0 0 4zm.8 2h3a15.6 15.6 0 0 0 1.3 3.8A8 8 0 0 1 5.1 16zm3-8h-3a8 8 0 0 1 4.3-3.8A15.6 15.6 0 0 0 8.1 8zM12 20c-.8-1.2-1.5-2.5-1.9-4h3.8c-.4 1.5-1.1 2.8-1.9 4zm2.3-6H9.7a14 14 0 0 1 0-4h4.6a14 14 0 0 1 0 4zm.3 5.8a15.6 15.6 0 0 0 1.3-3.8h3a8 8 0 0 1-4.3 3.8zm1.7-5.8a16 16 0 0 0 0-4h3.4a8 8 0 0 1 0 4z"/></svg>
        www.pulsemedia.co
      </li>
      <li class="wide">
        <svg viewBox="0 0 24 24" aria-hidden="true"><path d="M12 2a7 7 0 0 0-7 7c0 5.2 7 13 7 13s7-7.8 7-13a7 7 0 0 0-7-7zm0 9.5A2.5 2.5 0 1 1 12 6.5a2.5 2.5 0 0 1 0 5z"/></svg>
        42 Harbor Lane, Suite 3, North Block
      </li>
    </ul>

    <div class="brand"><span class="brand__name">pulse</span><span class="brand__dot"></span></div>
  </section>

</main>
</body>
</html>
```